Velmor Spire Nine Flash website

we need a website to cater to 2 aspect of the business. We have Velmor spire residence and velmor spire office. For the office, we will get their inquire and arrange a face to face meetup to show them the office area for rent. For the residence side, it will need to be like staylane or roomvio.com. we want to allow them to book online for the date they need. We have a total of 10 different room configurations starting at $70 per night and up depending on the size of the room. example of the design is https://brisquelodge.com/

Target Market(s)

the website should have detail information on the layout, designs, and luxury of the building.

Industry/Entity Type

office and service appartment rental/lease

Coding

Coded - Design and coding required

Number of Pages Required

5+ page

Requirements
Must have
• a luxury perspective
Nice to have
• example https://brisquelodge.com/

```html
<!DOCTYPE html>
<html lang="en">
<head>
<meta charset="utf-8">
<title>Velmor Spire Nine — Tower Office</title>
<link href="https://fonts.googleapis.com/css2?family=Montserrat:wght@400;500;600;700&display=swap" rel="stylesheet">
<style>
:root{
  --gold:#d3a437;
  --gold-dark:#b98c25;
  --ink:#1f1f1f;
  --muted:#5a5a5a;
  --light:#efefef;
  --white:#ffffff;
  --footer:#f4f4f4;
}
*{box-sizing:border-box;margin:0;padding:0}
html,body{width:1200px;height:3284px;overflow:hidden}
body{font-family:"Montserrat",sans-serif;color:var(--ink);background:var(--white);position:relative}
.abs{position:absolute}
.btn{display:inline-flex;align-items:center;justify-content:center;background:var(--gold);color:var(--white);font-size:15px;font-weight:600;letter-spacing:1px;text-transform:uppercase}
.btn-outline{background:transparent;border:2px solid var(--gold);color:var(--gold)}
.photo{position:absolute}

/* header */
.site-header{top:0;left:0;width:1200px;height:72px;display:flex;align-items:center;justify-content:space-between;padding:0 80px}
.brand{display:flex;align-items:center;gap:10px;font-size:14px;font-weight:600;color:var(--gold);letter-spacing:1px}
.brand-mark{width:22px;height:22px;border:2px solid var(--gold)}
.main-nav{display:flex;align-items:center;gap:36px;font-size:15px;font-weight:500;letter-spacing:1px}
.main-nav .btn{width:136px;height:44px}

/* tabs */
.tabs{top:108px;left:430px;width:340px;height:34px;display:flex;background:#e8e8e8;border-radius:18px;font-size:14px;font-weight:500}
.tab{flex:1;display:flex;align-items:center;justify-content:center;color:var(--muted)}
.tab.active{background:var(--white);border-radius:18px;color:var(--ink);font-weight:600}

/* hero */
.hero{top:144px;left:0;width:1200px;height:496px;background:linear-gradient(120deg,#6d5a4b,#a39486 45%,#5b5048)}
.hero-shade{top:144px;left:0;width:1200px;height:496px;background:rgba(0,0,0,.28)}
.hero-title{top:290px;left:0;width:1200px;text-align:center;color:var(--white);font-size:40px;font-weight:700;line-height:50px}
.hero-sub{top:392px;left:0;width:1200px;text-align:center;color:var(--white);font-size:18px}
.date-field{top:430px;left:282px;width:412px;height:42px;background:var(--white);display:flex;align-items:center;gap:12px;padding:0 14px;font-size:15px;color:var(--muted)}
.hero-btn{top:430px;left:704px;width:216px;height:42px}

/* features */
.feature-text h3{font-size:22px;font-weight:700;line-height:30px;margin-bottom:14px}
.feature-text p{font-size:15px;line-height:24px;color:var(--muted)}

/* tour band */
.tour-band{top:1344px;left:0;width:1200px;height:288px;background:var(--light)}
.tour-text{top:1384px;left:100px;width:560px}
.tour-text h2{font-size:24px;font-weight:700;line-height:32px;margin-bottom:18px}
.tour-text p{font-size:15px;line-height:24px;color:var(--muted)}
.tour-btn{top:1424px;left:884px;width:216px;height:44px}

/* testimonial */
.quote-mark{top:2010px;left:100px;font-size:90px;font-weight:700;color:#c8c8c8;line-height:90px}
.testimonial{top:2092px;left:100px;width:500px}
.testimonial blockquote{font-size:21px;font-weight:700;line-height:29px;margin-bottom:14px}
.testimonial p{font-size:13px;line-height:20px;color:var(--muted)}
.learn-btn{top:2322px;left:100px;width:148px;height:40px;font-size:13px}
.person-name{top:2330px;left:656px;color:var(--white);font-size:15px;font-weight:600}
.person-role{top:2352px;left:656px;color:var(--white);font-size:12px}

/* cta */
.cta{top:2448px;left:88px;width:1024px;height:144px;background:var(--gold);display:flex;align-items:center;justify-content:space-between;padding:0 50px}
.cta h2{color:var(--white);font-size:30px;font-weight:600;line-height:38px}
.cta .btn{background:var(--white);color:var(--ink);width:184px;height:44px}

.gallery-caption{top:2838px;left:32px;color:var(--white);font-size:18px;font-weight:600}

/* footer */
.site-footer{top:2880px;left:0;width:1200px;height:320px;background:var(--footer)}
.footer-brand{top:2932px;left:120px}
.footer-brand .brand{margin-bottom:14px}
.footer-brand p{font-size:14px;line-height:22px;color:var(--muted);width:200px}
.footer-nav{top:2968px;left:406px;display:flex;flex-direction:column;gap:30px;font-size:15px}
.footer-contact{top:2968px;left:532px;font-size:15px;line-height:24px}
.footer-contact h4,.footer-sub h4{font-size:16px;font-weight:700;margin-bottom:14px}
.footer-contact .gap{margin-top:22px}
.footer-sub{top:2968px;left:788px;width:290px}
.footer-sub p{font-size:14px;color:var(--muted);margin-bottom:16px}
.sub-form{display:flex;height:34px;margin-bottom:14px}
.sub-form span{flex:1;background:var(--white);border:1px solid #ddd;font-size:12px;color:#999;display:flex;align-items:center;padding:0 10px}
.sub-form b{width:84px;background:var(--gold);color:var(--white);font-size:12px;font-weight:600;display:flex;align-items:center;justify-content:center}
.footer-sub small{font-size:11px;line-height:16px;color:var(--muted);display:block}
.follow-bar{top:3208px;left:88px;width:1024px;height:64px;background:var(--gold);display:flex;align-items:center;justify-content:space-between;padding:0 40px;color:var(--white);font-size:20px;font-weight:500}
.social{display:flex;gap:16px}
.social i{width:20px;height:20px;border-radius:50%;border:2px solid var(--white);display:block}
</style>
</head>
<body>

<header class="site-header abs">
  <div class="brand"><span class="brand-mark"></span>VELMOR SPIRE</div>
  <nav class="main-nav">
    <span>LOCATION</span><span>EXPERIENCE</span><span>ABOUT US</span>
    <span class="btn btn-outline">CONTACT US</span>
  </nav>
</header>

<div class="tabs abs"><span class="tab">Tower Residence</span><span class="tab active">Tower Office</span></div>

<div class="hero photo" role="img" aria-label="Team collaborating around a desk in a bright shared office"></div>
<div class="hero-shade abs"></div>
<h1 class="hero-title abs">Unleash Your<br>Potential in Our Inspiring Offices</h1>
<p class="hero-sub abs">Partner with us to find the perfect office space for your growing business.</p>
<div class="date-field abs">
  <svg width="16" height="16" viewBox="0 0 16 16"><rect x="1" y="3" width="14" height="12" fill="none" stroke="#1f1f1f" stroke-width="1.6"/><line x1="1" y1="7" x2="15" y2="7" stroke="#1f1f1f" stroke-width="1.6"/><line x1="5" y1="1" x2="5" y2="4" stroke="#1f1f1f" stroke-width="1.6"/><line x1="11" y1="1" x2="11" y2="4" stroke="#1f1f1f" stroke-width="1.6"/></svg>
  Date
</div>
<div class="hero-btn btn abs">Schedule a tour</div>

<div class="photo" style="top:704px;left:0;width:580px;height:264px;background:linear-gradient(135deg,#8c8780,#d8d3cb 55%,#6e6963)" role="img" aria-label="Meeting room with a long table and office chairs"></div>
<div class="feature-text abs" style="top:772px;left:632px;width:480px">
  <h3>Professional Meeting Space</h3>
  <p>A professional meeting space that will make a positive impression on your clients and A well-appointed conference room with a modern design.</p>
</div>

<div class="feature-text abs" style="top:1056px;left:100px;width:500px">
  <h3>A well-lit conference room with a large rectangular table and chairs</h3>
  <p>This image depicts a spacious and well-lit conference room furnished with a large rectangular table and several chairs. The table is made of wood and has a white tablecloth, while the chairs are made of plastic and have wheels.</p>
</div>
<div class="photo" style="top:1008px;left:620px;width:580px;height:264px;background:linear-gradient(135deg,#4a4744,#9c958c 50%,#2f2d2b)" role="img" aria-label="Conference room with a large table and black chairs"></div>

<div class="tour-band abs"></div>
<div class="tour-text abs">
  <h2>Discover Your Ideal Workspace:<br>Explore Our Office with a Video Tour</h2>
  <p>Picture your team flourishing in a workspace designed to foster creativity, productivity, and success. Take a virtual tour of our office and discover the perfect setting for your business to thrive.</p>
</div>
<div class="tour-btn btn abs">Schedule a tour</div>

<div class="photo" style="top:1632px;left:0;width:1200px;height:328px;background:linear-gradient(120deg,#5c5a58,#a8a39b 45%,#6b5f55)" role="img" aria-label="Colleagues working at computers in an open office"></div>
<svg class="abs" style="top:1780px;left:592px" width="16" height="18" viewBox="0 0 16 18"><polygon points="0,0 16,9 0,18" fill="#ffffff"/></svg>

<div class="quote-mark abs">&ldquo;</div>
<div class="testimonial abs">
  <blockquote>&ldquo;I highly recommend this website to anyone looking for office space. The listings are comprehensive and easy to navigate, and the customer service is top-notch.&rdquo;</blockquote>
  <p>I was particularly impressed with the website's ability to filter listings by location, size, and price. This made it easy to find the perfect space for my needs. This is the only office rental website you'll ever need.</p>
</div>
<div class="learn-btn btn btn-outline abs">Learn more</div>
<div class="photo" style="top:2008px;left:632px;width:468px;height:380px;background:linear-gradient(160deg,#9a9590,#5d5650 60%,#3d3834)" role="img" aria-label="Portrait of a smiling client"></div>
<div class="person-name abs">Marta Quillen</div>
<div class="person-role abs">Product Manager at Lumera</div>

<section class="cta abs">
  <h2>Looking forward to<br>visit in person</h2>
  <span class="btn">Book a tour</span>
</section>

<div class="photo" style="top:2592px;left:0;width:600px;height:288px;background:linear-gradient(160deg,#b9b6b0,#7c7b74 55%,#4a4a44)" role="img" aria-label="Office lounge with large windows"></div>
<div class="photo" style="top:2592px;left:600px;width:600px;height:288px;background:linear-gradient(160deg,#a57a52,#6d4a2f 55%,#3e2b1c)" role="img" aria-label="Library corner with bookshelves and pendant lights"></div>
<div class="gallery-caption abs">Office work so relaxed</div>

<footer class="site-footer abs"></footer>
<div class="footer-brand abs">
  <div class="brand"><span class="brand-mark"></span>VELMOR SPIRE</div>
  <p>We have Velmor spire residence and velmor spire office.</p>
</div>
<nav class="footer-nav abs"><span>Location</span><span>Experience</span><span>About us</span></nav>
<div class="footer-contact abs">
  <h4>Contact information</h4>
  <div>(000) 000 000</div>
  <div>info@velmorspire.com</div>
  <h4 class="gap">Address</h4>
  <div>Velmor Spire Marketing Gallery</div>
  <div>Floor Street 21 City</div>
</div>
<div class="footer-sub abs">
  <h4>Subscribe</h4>
  <p>Join our mailing list for new updates</p>
  <div class="sub-form"><span>Enter email address</span><b>Subscribe</b></div>
  <small>By subscribing you agree to our Privacy Policy and consent to receive updates.</small>
</div>
<div class="follow-bar abs">
  <span>Follow us</span>
  <div class="social"><i></i><i></i><i></i></div>
</div>

</body>
</html>
```